New bussiness card, using company logo.
Lionel Brisk
Manager/Director
Brisk Property Developments
Po Box 5347
Thuringowa Central
Qld
0491 638 205
lionel@briskpropertydevelopments
eye catching, vibrant colours, professional

```html
<!DOCTYPE html>
<html lang="en">
<head>
<meta charset="utf-8">
<title>Brisk Property Developments – Business Cards</title>
<link href="https://fonts.googleapis.com/css2?family=Source+Sans+3:wght@400;700&display=swap" rel="stylesheet">
<style>
  :root {
    --backdrop: #2b2624;
    --card-red: #e0232d;
    --card-green-start: #9dca3f;
    --card-green-end: #5fb646;
    --card-grey: #6d6e70;
    --ink-light: #ffffff;
    --card-radius: 22px;
  }
  html, body {
    margin: 0;
    padding: 0;
    overflow: hidden;
  }
  body {
    width: 1200px;
    height: 723px;
    background: var(--backdrop);
    font-family: "Source Sans 3", "Myriad Pro", Arial, sans-serif;
    color: var(--ink-light);
    position: relative;
  }
  .card {
    position: absolute;
    width: 545px;
    height: 312px;
    border-radius: var(--card-radius);
    text-align: center;
  }
  .card--red   { left: 35px;  top: 32px;  background: var(--card-red); }
  .card--green { left: 624px; top: 32px;  background: linear-gradient(90deg, var(--card-green-start), var(--card-green-end)); }
  .card--grey  { left: 355px; top: 380px; height: 310px; background: var(--card-grey); }

  .brand-name {
    position: absolute;
    left: 0;
    right: 0;
    margin: 0;
    font-weight: 700;
    font-size: 36px;
    line-height: 1;
    letter-spacing: 0.3px;
  }
  .brand-name--stacked {
    top: 70px;
    font-size: 46px;
    line-height: 1.02;
  }
  .card--green .brand-name:not(.brand-name--stacked) { top: 110px; }
  .card--grey .brand-name:not(.brand-name--stacked)  { top: 110px; }

  .services {
    position: absolute;
    left: 0;
    right: 0;
    margin: 0;
    padding: 0;
    list-style: none;
    font-size: 24px;
    line-height: 1;
    display: flex;
    justify-content: center;
    gap: 14px;
  }
  .services li::before {
    content: "•";
    margin-right: 5px;
  }
  .card--red .services   { top: 217px; }
  .card--green .services { top: 205px; }
  .card--grey .services  { top: 204px; }

  .website {
    position: absolute;
    left: 0;
    right: 0;
    top: 272px;
    font-size: 15px;
    letter-spacing: 1.1px;
    line-height: 1;
  }
</style>
</head>
<body>
  <section class="card card--red">
    <h2 class="brand-name brand-name--stacked">Brisk Property<br>Developments</h2>
    <ul class="services">
      <li>Demolish</li>
      <li>Renovate</li>
      <li>New Constructions</li>
    </ul>
    <div class="website">www.briskpropertydevelopments.com</div>
  </section>

  <section class="card card--green">
    <h2 class="brand-name">Brisk Property Developments</h2>
    <ul class="services">
      <li>Demolish</li>
      <li>Renovate</li>
      <li>New Constructions</li>
    </ul>
    <div class="website">www.briskpropertydevelopments.com</div>
  </section>

  <section class="card card--grey">
    <h2 class="brand-name">Brisk Property Developments</h2>
    <ul class="services">
      <li>Demolish</li>
      <li>Renovate</li>
      <li>New Constructions</li>
    </ul>
    <div class="website">www.briskpropertydevelopments.com</div>
  </section>
</body>
</html>
```